TK Homes - Stone Dorf Design

Looking for a double sides design, 1 side for my realestate and the other for home building. ( TK Homes on 1 side, Stone Dorf card on the other Side
Side 1 - Marek Tove ~ Vox Realty logo and Company ( the Property quarter )
Marek Tove
Marek@Marektove.example
IG - Marek_Bzq_Realtor
FB - marekt
Cell - 5558130467
3847 61 St Nw

Side 2
Marek Tove
5558130467
IG - Stonedorf_Bzq
Stonedorfdev@mailbox.example

Target Market(s)

Home buyers/ sellers

Industry/Entity Type

Home builders - Realestate

Contact Information for Business Card

Above

Requirements
Must have
• Black OR White background - my information -

```html
<!DOCTYPE html>
<html lang="en">
<head>
<meta charset="utf-8">
<title>TK Homes – Stone Dorf Design business cards</title>
<link rel="stylesheet" href="https://fonts.googleapis.com/css2?family=Libre+Baskerville:wght@400;700&family=Tinos:wght@400&display=swap">
<style>
  :root {
    --page-bg: #e6e6e8;
    --card-bg: #ffffff;
    --brand-blue: #1f6fbf;
    --brand-gold: #f2c23a;
    --ink: #1a1a1a;
    --rule: #111111;
  }
  * { box-sizing: border-box; margin: 0; padding: 0; }
  html, body {
    width: 1200px; height: 780px; overflow: hidden;
    background: var(--page-bg);
  }
  .canvas {
    position: relative; width: 1200px; height: 780px;
  }
  .card {
    position: absolute; top: 230px;
    width: 560px; height: 320px;
    background: var(--card-bg);
    box-shadow: 0 6px 18px rgba(0,0,0,.18);
    overflow: hidden;
    font-family: "Tinos", "Times New Roman", serif;
    color: var(--ink);
  }
  .card--realty { left: 30px; }
  .card--builder { left: 610px; }

  .brand {
    position: absolute; left: 34px; top: 36px;
    display: flex; align-items: center; gap: 10px;
    font-family: "Libre Baskerville", Georgia, serif;
    font-weight: 400; font-size: 30px; letter-spacing: 1px;
    color: var(--brand-blue);
  }
  .brand__mark {
    width: 14px; height: 14px; background: var(--brand-gold);
  }

  .divider {
    position: absolute; left: 34px; top: 118px;
    width: 452px; height: 1px; background: var(--rule);
  }

  .holder {
    position: absolute; right: 64px; top: 78px; text-align: right;
  }
  .holder__name {
    font-family: "Libre Baskerville", Georgia, serif;
    font-weight: 700; font-size: 25px; line-height: 1;
    color: var(--brand-blue);
  }
  .holder__name .surname { color: var(--brand-gold); }
  .holder__role {
    margin-top: 12px;
    font-family: "Libre Baskerville", Georgia, serif;
    font-weight: 700; font-size: 14px;
  }

  .accent-tab {
    position: absolute; right: 0; top: 70px;
    width: 26px; height: 58px; background: var(--brand-blue);
  }

  .contacts {
    position: absolute; left: 34px; top: 138px;
    list-style: none; font-size: 15px; line-height: 21px;
  }
  .contacts li { display: flex; align-items: center; gap: 8px; }
  .contacts svg { width: 12px; height: 12px; flex: none; }

  .address {
    position: absolute; right: 44px; bottom: 26px;
    font-size: 19px;
  }
</style>
</head>
<body>
<main class="canvas">

  <section class="card card--realty" aria-label="Realty side">
    <div class="brand">Marek Tove</div>
    <div class="holder">
      <p class="holder__name">Marek <span class="surname">Tove</span></p>
      <p class="holder__role">Director</p>
    </div>
    <div class="divider"></div>
    <div class="accent-tab"></div>
    <ul class="contacts">
      <li><svg viewBox="0 0 12 12"><path d="M3 1 L5 3.5 L4 5 Q5 7 7 8 L8.5 7 L11 9 L9.5 11 Q4 10.5 1 3 Z" fill="var(--brand-blue)"/></svg>5558130467</li>
      <li><svg viewBox="0 0 12 12"><circle cx="6" cy="6" r="5.5" fill="var(--brand-blue)"/></svg>marekt</li>
      <li><svg viewBox="0 0 12 12"><rect x="1" y="1" width="10" height="10" rx="2" fill="none" stroke="var(--brand-blue)" stroke-width="1.5"/></svg>Marek_Bzq_Realtor</li>
      <li><svg viewBox="0 0 12 12"><rect x="0.5" y="2" width="11" height="8" fill="var(--brand-blue)"/><path d="M0.5 2 L6 6.5 L11.5 2" fill="none" stroke="#fff" stroke-width="1"/></svg>Marek@Marektove.example</li>
      <li><svg viewBox="0 0 12 12"><circle cx="6" cy="6" r="5" fill="none" stroke="var(--brand-blue)" stroke-width="1.3"/><path d="M1 6 H11 M6 1 Q3 6 6 11 M6 1 Q9 6 6 11" fill="none" stroke="var(--brand-blue)" stroke-width="1"/></svg>www.marektove.example</li>
    </ul>
    <p class="address">3847 61 St Nw</p>
  </section>

  <section class="card card--builder" aria-label="Home building side">
    <div class="brand"><span>Stone Dorf</span><span class="brand__mark"></span></div>
    <div class="holder">
      <p class="holder__name">Marek <span class="surname">Tove</span></p>
      <p class="holder__role">Director</p>
    </div>
    <div class="divider"></div>
    <div class="accent-tab"></div>
    <ul class="contacts">
      <li><svg viewBox="0 0 12 12"><path d="M3 1 L5 3.5 L4 5 Q5 7 7 8 L8.5 7 L11 9 L9.5 11 Q4 10.5 1 3 Z" fill="var(--brand-blue)"/></svg>5558130467</li>
      <li><svg viewBox="0 0 12 12"><rect x="1" y="1" width="10" height="10" rx="2" fill="none" stroke="var(--brand-blue)" stroke-width="1.5"/></svg>Stonedorf_Bzq</li>
      <li><svg viewBox="0 0 12 12"><rect x="0.5" y="2" width="11" height="8" fill="var(--brand-blue)"/><path d="M0.5 2 L6 6.5 L11.5 2" fill="none" stroke="#fff" stroke-width="1"/></svg>Stonedorfdev@mailbox.example</li>
    </ul>
  </section>

</main>
</body>
</html>
```